Courses Report - Analytics Redesign

We are a Learning Management System company that is looking to redesign our reporting suite in our product. We would like to add more graphs and visualizations to our reporting help communicate results and give our reporting a more modern look. Screenshots include our current courses report so that you can see the filters and type of data that our users search for. We are using Varno Metrics as our reporting service and please see https://www.varnometrics-demo.net/visual-gallery/ for examples of what type of visualizations can be generated.

Target Market(s)

LMS Administrators, Marketing and Sales Product Trainers

Number of Pages Required

1 page

Font styles to use
Sans Serif

Colors
33b8a4
33a6d7
0392cd
00a990
85cae6
87cfc6
cadf82
abd036
9bcb3b

Requirements
Must have
• Clean and simple look. Use Raleway as font. Easy to use and intuitive filtering. Ability to add/remove filters to the output. Graphical display of results that can drill down.
Nice to have
• Better way of listing other reports in menu on left.
Should not have
• Complicated graphs that cannot be easily understood.

```html
<!DOCTYPE html>
<html lang="en">
<head>
<meta charset="utf-8">
<title>Courses Report</title>
<link href="https://fonts.googleapis.com/css2?family=Raleway:wght@400;500;600;700&display=swap" rel="stylesheet">
<style>
:root{
  --bg:#f3f5f7;--white:#fff;--ink:#1d2b33;--muted:#8a969c;--text:#4a5a62;
  --green:#9bcb3b;--lime:#cadf82;--teal:#87cfc6;--cyan:#22b5d5;--line:#e3e8ea;
  --head:#d9e3e6;--stripe:#f7f9fa;--grey-btn:#8f9ea5;
}
*{box-sizing:border-box;margin:0;padding:0}
html,body{width:1200px;height:799px;overflow:hidden}
body{font-family:'Raleway',sans-serif;background:var(--bg);color:var(--text);position:relative}
.abs{position:absolute}
.topbar{left:0;top:0;width:1200px;height:56px;background:var(--white);border-bottom:1px solid var(--line)}
.brand{left:50px;top:16px;display:flex;align-items:center;gap:8px;font-size:16px;font-weight:700;color:#2f4a3a}
.brand-dot{width:22px;height:22px;border-radius:50%;background:var(--green)}
.nav a{position:absolute;top:20px;transform:translateX(-50%);font-size:11px;color:var(--muted);text-decoration:none;white-space:nowrap}
.nav a.active{color:var(--ink);font-weight:500}
.nav a.active::after{content:"";position:absolute;left:0;right:0;top:19px;height:2px;background:var(--cyan)}
.user{left:1022px;top:14px;display:flex;align-items:center;gap:8px;font-size:11px;color:var(--ink)}
.avatar{width:28px;height:28px;border-radius:50%;background:#e6f1cf;color:var(--green);display:flex;align-items:center;justify-content:center;font-size:15px;font-weight:600}
.subbar{left:0;top:56px;width:1200px;height:56px;background:var(--white)}
.subnav a{top:80px}
.subnav a.active::after{top:18px}
.page-title{left:50px;top:144px;font-size:19px;font-weight:500;color:var(--ink)}
.btn{display:flex;align-items:center;justify-content:center;border-radius:3px;font-size:11px;font-weight:500}
.btn-filter{left:969px;top:142px;width:82px;height:28px;background:var(--green);color:#fff;gap:6px}
.btn-results{left:1060px;top:142px;width:90px;height:28px;background:var(--lime);color:var(--ink)}
.card{background:var(--white);border-radius:2px}
.card-title{position:absolute;left:19px;top:19px;font-size:9px;letter-spacing:1px;font-weight:600;color:#55636a}
.panel{left:986px;top:179px;width:164px;height:205px;background:var(--white);box-shadow:0 3px 10px rgba(0,0,0,.1);border-radius:2px}
.mini{position:absolute;top:13px;height:15px;width:40px;border-radius:2px;color:#fff;font-size:10px;font-weight:600;display:flex;align-items:center;justify-content:center}
.mini.go{left:64px;background:var(--green)}
.mini.reset{left:111px;background:var(--grey-btn)}
.field-label{position:absolute;left:13px;font-size:10px;font-weight:500;color:var(--ink)}
.select{position:absolute;left:13px;width:138px;height:24px;border:1px solid #d5dcdf;border-radius:2px;font-size:10px;color:var(--text);padding:0 8px;display:flex;align-items:center;justify-content:space-between}
.select::after{content:"";width:4px;height:4px;border-right:1px solid #777;border-bottom:1px solid #777;transform:rotate(45deg);margin-top:-3px}
table.report{position:absolute;left:50px;top:467px;width:1100px;border-collapse:collapse;font-size:10px}
.report th{height:31px;background:var(--head);text-align:left;font-weight:600;color:var(--ink);font-size:9px}
.report td{height:37.6px;color:#4b5a61}
.report tr:nth-child(even) td{background:var(--stripe)}
.report tbody tr:nth-child(odd) td{background:var(--white)}
.chk{display:inline-block;width:15px;height:15px;border:1px solid #bfc9cd;border-radius:2px;background:#fff;vertical-align:middle}
.report th .chk{background:var(--head);border-color:#9eadb3}
.pager{left:50px;top:741px;font-size:10px;color:var(--ink)}
svg text{font-family:'Raleway',sans-serif}
</style>
</head>
<body>
<header class="abs topbar">
  <div class="abs brand"><span class="brand-dot"></span>Learnwell Hub</div>
  <nav class="nav">
    <a style="left:358px">Home</a><a style="left:419px">Users</a><a class="active" style="left:485px">Reports</a><a style="left:555px">Content</a><a style="left:617px">Site</a>
  </nav>
  <div class="abs user"><span class="avatar">M</span>Mara Kessler <span style="font-size:8px;color:var(--muted)">&#8964;</span></div>
</header>
<div class="abs subbar"></div>
<nav class="nav subnav">
  <a style="left:377px">Saved Reports</a><a style="left:458px">Users</a><a class="active" style="left:526px">Courses</a><a style="left:602px">Due Dates</a><a style="left:712px">Classroom Enrollment</a><a style="left:831px">Course Survey</a><a style="left:943px">Satisfaction Survey</a><a style="left:1061px">Purchase History</a>
</nav>

<h1 class="abs page-title">Courses</h1>
<div class="abs btn btn-filter">
  <svg width="12" height="10" viewBox="0 0 12 10" fill="none" stroke="#fff" stroke-width="1"><path d="M0 2h12M0 5h12M0 8h12"/><circle cx="8" cy="2" r="1.3" fill="#9bcb3b"/><circle cx="4" cy="5" r="1.3" fill="#9bcb3b"/><circle cx="8" cy="8" r="1.3" fill="#9bcb3b"/></svg>Filter</div>
<div class="abs btn btn-results">Filter results</div>

<section class="abs card" style="left:50px;top:186px;width:350px;height:256px">
  <h2 class="card-title">TOP LEARNERS</h2>
  <svg class="abs" style="left:0;top:0" width="350" height="256" viewBox="62 233 438 320">
    <g stroke="#e6eaec" stroke-dasharray="2 2">
      <path d="M213 294V488M264 294V488M315 294V488M365 294V488M415 294V488M466 294V488"/>
      <path d="M162 294H466M162 326H466M162 358H466M162 390H466M162 422H466M162 456H466"/>
    </g>
    <path d="M162 294V488" stroke="#8c989d"/>
    <g fill="#cadf82"><rect x="163" y="309" width="290" height="6"/><rect x="163" y="373" width="147" height="6"/><rect x="163" y="437" width="82" height="6"/></g>
    <g fill="#87cfc6"><rect x="163" y="341" width="190" height="6"/><rect x="163" y="405" width="128" height="6"/><rect x="163" y="469" width="34" height="6"/></g>
    <g font-size="8" fill="#3a4a52" text-anchor="end">
      <text x="154" y="315">Jonah Smits</text><text x="154" y="347">Ewan Glenby</text><text x="154" y="379">Melina Bridges</text><text x="154" y="411">Viktor Morland</text><text x="154" y="439">Lucia Lyell</text><text x="154" y="475">Penny Hurst</text>
    </g>
    <g font-size="9" fill="#55636a" text-anchor="middle">
      <text x="162" y="503">0</text><text x="213" y="503">10</text><text x="264" y="503">20</text><text x="315" y="503">30</text><text x="365" y="503">40</text><text x="415" y="503">50</text><text x="466" y="503">60</text>
    </g>
  </svg>
</section>

<section class="abs card" style="left:425px;top:186px;width:725px;height:256px">
  <h2 class="card-title">COMPLETED COURSES</h2>
  <svg class="abs" style="left:0;top:0" width="725" height="256" viewBox="531 233 906 320">
    <g stroke="#e6eaec" stroke-dasharray="2 2">
      <path d="M580 294H1407M580 359H1407M580 423H1407"/>
      <path d="M656 294V488M728 294V488M796 294V488M864 294V488M932 294V488M1000 294V488M1068 294V488M1136 294V488M1204 294V488M1272 294V488M1340 294V488"/>
    </g>
    <path d="M580 488H1407" stroke="#8c989d"/>
    <g font-size="9" fill="#55636a" text-anchor="end"><text x="567" y="297">15</text><text x="567" y="362">10</text><text x="567" y="426">5</text><text x="567" y="491">0</text></g>
    <g fill="#cadf82">
      <rect x="609" y="404" width="7" height="84"/><rect x="677" y="434" width="7" height="54"/><rect x="745" y="404" width="7" height="84"/><rect x="813" y="442" width="7" height="46"/><rect x="881" y="428" width="7" height="60"/><rect x="949" y="362" width="7" height="126"/><rect x="1017" y="381" width="7" height="107"/><rect x="1085" y="404" width="7" height="84"/><rect x="1153" y="404" width="7" height="84"/><rect x="1221" y="438" width="7" height="50"/><rect x="1289" y="420" width="7" height="68"/><rect x="1357" y="430" width="7" height="58"/>
    </g>
    <g fill="#87cfc6">
      <rect x="625" y="468" width="7" height="20"/><rect x="693" y="422" width="7" height="66"/><rect x="761" y="442" width="7" height="46"/><rect x="829" y="374" width="7" height="114"/><rect x="897" y="428" width="7" height="60"/><rect x="965" y="468" width="7" height="20"/><rect x="1033" y="453" width="7" height="35"/><rect x="1101" y="442" width="7" height="46"/><rect x="1169" y="478" width="7" height="10"/><rect x="1237" y="478" width="7" height="10"/><rect x="1305" y="478" width="7" height="10"/><rect x="1373" y="484" width="7" height="4"/>
    </g>
    <polyline fill="none" stroke="#22b5d5" stroke-width="1.5" points="620,387 688,427 759,397 823,404 893,377 962,382 1027,417 1097,440 1165,430 1232,401 1300,372 1368,384"/>
    <g fill="#22b5d5">
      <circle cx="620" cy="387" r="3.5"/><circle cx="688" cy="427" r="3.5"/><circle cx="759" cy="397" r="3.5"/><circle cx="823" cy="404" r="3.5"/><circle cx="893" cy="377" r="3.5"/><circle cx="962" cy="382" r="3.5"/><circle cx="1027" cy="417" r="3.5"/><circle cx="1097" cy="440" r="3.5"/><circle cx="1165" cy="430" r="3.5"/><circle cx="1232" cy="401" r="3.5"/>
    </g>
    <g font-size="9" fill="#55636a" text-anchor="middle">
      <text x="620" y="503">Jan</text><text x="692" y="503">Feb</text><text x="763" y="503">Mar</text><text x="830" y="503">Apr</text><text x="897" y="503">May</text><text x="966" y="503">Jun</text><text x="1034" y="503">July</text><text x="1101" y="503">Aug</text><text x="1170" y="503">Sept</text><text x="1237" y="503">Oct</text><text x="1306" y="503">Nov</text><text x="1373" y="503">Dec</text>
    </g>
    <g font-size="11" fill="#55636a">
      <path d="M833 531H851" stroke="#22b5d5" stroke-width="1.5"/><circle cx="842" cy="531" r="3.5" fill="#22b5d5"/><text x="857" y="535">Completed</text>
      <rect x="949" y="526" width="11" height="10" fill="#cadf82"/><text x="967" y="535">In progress</text>
      <rect x="1059" y="526" width="11" height="10" fill="#87cfc6"/><text x="1077" y="535">Not started</text>
    </g>
  </svg>
</section>

<aside class="abs panel">
  <span class="mini go">Filter</span><span class="mini reset">Reset</span>
  <span class="field-label" style="top:36px">Year</span><div class="select" style="top:55px">2019</div>
  <span class="field-label" style="top:90px">Month</span><div class="select" style="top:110px">January</div>
  <span class="field-label" style="top:145px">Member</span><div class="select" style="top:165px">Viktor Morland</div>
</aside>

<table class="report">
  <thead><tr><th style="width:59px;padding-left:19px"><span class="chk"></span></th><th style="width:105px">First name</th><th style="width:117px">Last name</th><th style="width:176px">Email address</th><th style="width:304px">Course name</th><th style="width:115px">User status</th><th style="width:117px">Completion date</th><th>Job role</th></tr></thead>
  <tbody>
    <tr><td style="padding-left:19px"><span class="chk"></span></td><td>Viktor</td><td>Morland</td><td>viktorm@tagfield.net</td><td>Determining Customer Needs</td><td>Completed</td><td>04/21/2016</td><td>Manager</td></tr>
    <tr><td style="padding-left:19px"><span class="chk"></span></td><td>Jonah</td><td>Smits</td><td>jonah.smits@mailnest.com</td><td>5 Management Mistakes Blocking Sales Reps from Selling</td><td>Completed</td><td>01/17/2019</td><td>Sales rep</td></tr>
    <tr><td style="padding-left:19px"><span class="chk"></span></td><td>Penny</td><td>Hurst</td><td>penny.hurst@postbox.net</td><td>PDF -- The LMS Evaluation Checklist</td><td>Completed</td><td>04/21/2016</td><td>Manager</td></tr>
    <tr><td style="padding-left:19px"><span class="chk"></span></td><td>Lucia</td><td>Lyell</td><td>lucialyell@tagfield.net</td><td>Health and Wellness</td><td>Completed</td><td>01/25/2019</td><td>Sales rep</td></tr>
    <tr><td style="padding-left:19px"><span class="chk"></span></td><td>Viktor</td><td>Morland</td><td>viktorm@tagfield.net</td><td>Determining Customer Needs</td><td>Completed</td><td>04/21/2016</td><td>Manager</td></tr>
    <tr><td style="padding-left:19px"><span class="chk"></span></td><td>Ewan</td><td>Glenby</td><td>ewan.glenby@mailnest.com</td><td>Health and Wellness</td><td>Completed</td><td>10/29/2018</td><td>Manager</td></tr>
  </tbody>
</table>
<p class="abs pager">Showing page 1 of 1</p>
</body>
</html>
```